Tech Savy small Business accountant business card design

We need a business card for a new company based in the cloud. We provide tax, business advisory, accounting, information technology solutions and back office functions to small businesses. We offer fixed fee packages with add on services as you need them. By harnessing technology we simplify small business operational processes providing valuable time and information for small business owners to grow their business. In the logo (bluvoria) we want to be able to see bluv and experts. The final design should communicate achieving growth dreams and balance (ie life and $).
Updates
This project has been temporarily placed on hold until I finalize "Tech Savy small Business accountant needs a logo". I invite all designers to submit on this logo project. Once my logo is finalized I will resume this business card contest. Thanks Added Wednesday, March 19, 2014
This project has been temporarily placed on hold until I finalize "Tech Savy small Business accountant logo". I invite all designers to submit on this logo project. Once my logo is finalized I will resume this business card contest. Thanks Added Thursday, March 20, 2014
Target Market(s)
Small Business (Revenue $500,000, more than 3 employees) owners.
Industry/Entity Type
Small Business
Contact Information for Business Card
Marcy Elwind (Principal)
Accountant, Tax Agent.
TEL | 0417 683 912
EMAIL | Marcy.Elwind@bluvoria.com.au
WEB | www.bluvoria.com.au
Look and feel

```html
<!DOCTYPE html>
<html lang="en">
<head>
<meta charset="utf-8">
<title>bluvoria business card</title>
<link href="https://fonts.googleapis.com/css2?family=Open+Sans:wght@400;600;700&display=swap" rel="stylesheet">
<style>
  :root {
    --backdrop: #e8e6e2;
    --card: #ffffff;
    --blue: #1f88d0;
    --blue-light: #45b0e4;
    --blue-deep: #1670bd;
    --grey: #75787d;
    --grey-dark: #55585c;
  }
  * { box-sizing: border-box; margin: 0; padding: 0; }
  html, body {
    width: 1200px; height: 913px; overflow: hidden;
    background: var(--backdrop);
    font-family: "Open Sans", Arial, sans-serif;
  }
  .stage { position: relative; width: 1200px; height: 913px; }
  .card {
    position: absolute; top: 297px;
    width: 520px; height: 318px;
    background: var(--card);
    border-radius: 16px;
    overflow: hidden;
    box-shadow: 0 6px 18px rgba(0,0,0,.14);
  }
  .card--front { left: 50px; }
  .card--back { left: 630px; }

  .side-band {
    position: absolute; top: 0; bottom: 0; width: 46px;
    background: linear-gradient(180deg, var(--blue-light), var(--blue-deep));
  }
  .card--front .side-band { left: 0; }
  .card--back .side-band { right: 0; }

  .corner-tab {
    position: absolute; top: 26px; right: 0;
    width: 14px; height: 22px; background: var(--blue-light);
  }

  .wordmark {
    font-weight: 700; color: var(--blue); letter-spacing: -0.5px; line-height: 1;
  }
  .tagline { color: var(--grey); font-weight: 400; }

  .front-brand { position: absolute; top: 26px; right: 40px; text-align: left; }
  .front-brand .wordmark { font-size: 44px; }
  .front-brand .tagline { font-size: 12.5px; margin-top: 3px; }

  .contact { position: absolute; right: 24px; top: 128px; text-align: right; }
  .contact__name {
    font-size: 19px; font-weight: 700; color: var(--blue); letter-spacing: .3px;
  }
  .contact__role { font-size: 12.5px; color: var(--grey); margin-top: 1px; }
  .contact__list { list-style: none; margin-top: 12px; }
  .contact__item {
    font-size: 12.5px; color: var(--blue); line-height: 19px;
    display: flex; justify-content: flex-end; align-items: center; gap: 7px;
  }
  .contact__item svg { width: 11px; height: 11px; flex: none; }

  .rule {
    position: absolute; left: 46px; top: 158px; width: 210px; height: 1px;
    background: var(--blue);
  }

  .back-brand { position: absolute; left: 52px; top: 118px; }
  .back-brand .wordmark { font-size: 70px; }
  .back-brand .tagline { font-size: 18px; font-weight: 600; color: var(--grey-dark); margin-top: 6px; }
</style>
</head>
<body>
<main class="stage">
  <section class="card card--front" aria-label="Card front">
    <div class="side-band"></div>
    <div class="corner-tab"></div>
    <div class="front-brand">
      <div class="wordmark">bluvoria</div>
      <div class="tagline">Your business and accounting partner</div>
    </div>
    <div class="rule"></div>
    <div class="contact">
      <div class="contact__name">MARCY ELWIND (Principal)</div>
      <div class="contact__role">Accountant, Tax Agent</div>
      <ul class="contact__list">
        <li class="contact__item">0417 683 912
          <svg viewBox="0 0 12 12" aria-hidden="true"><path d="M2.5 1h2l1 3-1.3 1a6 6 0 0 0 2.8 2.8L8 6.5l3 1v2A1.5 1.5 0 0 1 9.5 11 8.5 8.5 0 0 1 1 2.5 1.5 1.5 0 0 1 2.5 1z" fill="none" stroke="#55585c" stroke-width="1"/></svg>
        </li>
        <li class="contact__item">www.bluvoria.com.au
          <svg viewBox="0 0 12 12" aria-hidden="true"><g fill="none" stroke="#55585c" stroke-width="1"><circle cx="6" cy="6" r="5"/><ellipse cx="6" cy="6" rx="2.2" ry="5"/><path d="M1 6h10"/></g></svg>
        </li>
        <li class="contact__item">Marcy.Elwind@bluvoria.com.au
          <svg viewBox="0 0 12 12" aria-hidden="true"><g fill="none" stroke="#55585c" stroke-width="1"><rect x="1" y="2.5" width="10" height="7"/><path d="M1 2.5l5 4 5-4"/></g></svg>
        </li>
      </ul>
    </div>
  </section>

  <section class="card card--back" aria-label="Card back">
    <div class="side-band"></div>
    <div class="back-brand">
      <div class="wordmark">bluvoria</div>
      <div class="tagline">Your business and accounting partner</div>
    </div>
  </section>
</main>
</body>
</html>
```